Stylish new business card needed!

Hello everyone! I am in need of a new business card design for an alarm company here in Hurricane WV. I have all fonts, color codes and logos provided for you use! We are a young company and like the style of a clean sleek looking business card. Would like it double sided, one side holding the logo and the other with your design!
Target Market(s)
The people that are looking for the newest tech for home automation and security
Industry/Entity Type
Alarm services; Home automation
Contact Information for Business Card
Name of person; position (Sales; Installer); Phone Number (555.418.7260); Employee cell Number; Website (www.GuardedByVelk.example); Employee Email; Double sided
Look and feel
Each slider illustrates characteristics of the customer's brand and the style your logo design should communicate.

```html
<!DOCTYPE html>
<html lang="en">
<head>
<meta charset="utf-8">
<title>Guarded By Velk – Business Card</title>
<link rel="stylesheet" href="https://fonts.googleapis.com/css2?family=Arimo:ital,wght@0,400;0,700;1,700&display=swap">
<style>
  :root {
    --stage: #2b2e34;
    --paper: #f4f4f4;
    --orange: #ec8a4c;
    --grey: #8c8c8c;
    --ink: #111111;
    --card-black: #1f1f23;
    --emboss: #141417;
    --emboss-edge: #2c2c31;
  }
  * { box-sizing: border-box; margin: 0; padding: 0; }
  html, body { width: 1200px; height: 780px; overflow: hidden; }
  body {
    background: var(--stage);
    font-family: "Arimo", Arial, sans-serif;
    display: flex;
    align-items: center;
    justify-content: center;
    gap: 40px;
  }
  .card {
    position: relative;
    width: 560px;
    height: 320px;
    overflow: hidden;
    box-shadow: 0 10px 30px rgba(0,0,0,.45);
  }
  /* Front */
  .card--front { background: var(--paper); }
  .front-wave { position: absolute; inset: 0; width: 100%; height: 100%; }
  .brand {
    position: absolute;
    left: 240px; top: 44px;
    color: var(--grey);
  }
  .brand__name {
    font-size: 34px;
    font-weight: 700;
    letter-spacing: 1px;
    line-height: 1;
  }
  .brand__tagline {
    margin-top: 8px;
    font-size: 7.5px;
    font-weight: 700;
    letter-spacing: .6px;
    text-transform: uppercase;
    color: var(--orange);
  }
  .person {
    position: absolute;
    left: 66px; top: 120px;
  }
  .person__name {
    font-size: 22px;
    font-weight: 700;
    font-style: italic;
  }
  .person__first { color: var(--orange); }
  .person__last { color: var(--grey); }
  .person__role {
    margin-top: 6px;
    margin-left: 50px;
    font-size: 13px;
    color: var(--ink);
  }
  .divider {
    position: absolute;
    left: 258px; top: 156px;
    width: 2px; height: 96px;
    background: var(--ink);
  }
  .contacts {
    position: absolute;
    left: 282px; top: 160px;
    list-style: none;
    font-size: 14px;
    color: var(--ink);
  }
  .contacts li {
    display: flex;
    align-items: center;
    gap: 8px;
    height: 22px;
  }
  .contacts svg { width: 12px; height: 12px; flex: none; }
  /* Back */
  .card--back {
    background: var(--card-black);
    display: flex;
    flex-direction: column;
    align-items: center;
    justify-content: center;
    color: var(--emboss);
    text-shadow: 0 1px 0 var(--emboss-edge);
  }
  .card--back .brand__name { font-size: 46px; color: var(--emboss); }
  .card--back .brand__tagline {
    margin-top: 12px;
    font-size: 10px;
    color: var(--emboss);
  }
</style>
</head>
<body>
  <section class="card card--front" aria-label="Business card front">
    <svg class="front-wave" viewBox="0 0 560 320" preserveAspectRatio="none" aria-hidden="true">
      <path d="M0 236 C 70 300, 280 322, 560 300 L560 320 L0 320 Z" fill="var(--orange)"/>
      <path d="M0 236 C 24 258, 40 268, 60 276 L0 320 Z" fill="var(--orange)"/>
      <path d="M10 238 C 80 290, 290 312, 540 296" fill="none" stroke="var(--grey)" stroke-width="3" stroke-linecap="round"/>
      <path d="M0 218 C 80 280, 300 306, 560 290 L560 320 L0 320 Z" fill="var(--orange)" opacity="0"/>
    </svg>

    <div class="brand">
      <div class="brand__name">GUARDED BY VELK</div>
      <div class="brand__tagline">Automation and Security Services</div>
    </div>

    <div class="person">
      <div class="person__name"><span class="person__first">Mara</span> <span class="person__last">Kovalenko</span></div>
      <div class="person__role">Sales; Installer</div>
    </div>

    <div class="divider"></div>

    <ul class="contacts">
      <li>
        <svg viewBox="0 0 12 12" aria-hidden="true"><path d="M2.5 1 L4.5 1 L5.2 3.6 L4 4.6 C4.6 6 6 7.4 7.4 8 L8.4 6.8 L11 7.5 L11 9.5 C11 10.3 10.3 11 9.5 11 C5 11 1 7 1 2.5 C1 1.7 1.7 1 2.5 1 Z" fill="var(--orange)"/></svg>
        555.418.7260
      </li>
      <li>
        <svg viewBox="0 0 12 12" aria-hidden="true"><rect x="3" y="0.8" width="6" height="10.4" rx="1.2" fill="none" stroke="var(--orange)" stroke-width="1.2"/><circle cx="6" cy="9.4" r=".7" fill="var(--orange)"/></svg>
        555.602.9134
      </li>
      <li>
        <svg viewBox="0 0 12 12" aria-hidden="true"><circle cx="6" cy="6" r="5" fill="none" stroke="var(--orange)" stroke-width="1.2"/><path d="M1 6 H11 M6 1 C3.5 3.5 3.5 8.5 6 11 M6 1 C8.5 3.5 8.5 8.5 6 11" fill="none" stroke="var(--orange)" stroke-width="1"/></svg>
        www.GuardedByVelk.example
      </li>
      <li>
        <svg viewBox="0 0 12 12" aria-hidden="true"><rect x="0.8" y="2.5" width="10.4" height="7.5" rx="1" fill="none" stroke="var(--orange)" stroke-width="1.2"/><path d="M1 3 L6 7 L11 3" fill="none" stroke="var(--orange)" stroke-width="1.2"/></svg>
        info@GuardedByVelk.example
      </li>
    </ul>
  </section>

  <section class="card card--back brand" aria-label="Business card back" style="position:relative;left:auto;top:auto;">
    <div class="brand__name">GUARDED BY VELK</div>
    <div class="brand__tagline">Automation and Security Services</div>
  </section>
</body>
</html>
```